KM Guild of Realtors

We are working with the Kestrel Meadow Guild of Realtors.

Some sites to use for content/competitors and inspiration:
https://www.plv.realtor
https://brimforthagent.com
https://qxagents.com
https://www.corvalhomeland.com
https://www.gwobel.com

Thank you for taking the time to consider designing a website for us. We are web developers based in Stockton, CA, USA. Most of our projects go through the same process. Understanding this process may help you win a project with us. We custom-code all of our websites in-house. We don’t have any requirements as to what tools you use for your design, but we prefer Figma files. For any design that we label as four-stars, we send it to the client for review. The client picks the final design they want us to use. Once we complete this process, we will continue to show additional clients all the four-star sites and purchase them later. Your designs will have multiple chances to sell. For better chances of success, we ask that you follow these guidelines.

IMAGES:
If you use any images or icons in the design, we ask that you have a link to the asset so we can purchase the image/icon. Most of the designs we submit do not have the customer’s images on them unless they have some great images. Be creative; show us the feeling you are trying to portray with your image choices. Use any royalty-free site you choose. We subscribe to Velkor and mainly use their images, but we can purchase images outside of Velkor.

PLEASE NOTE: we will not submit designs to clients with watermarks on the images.

FONTS:
We ask that you identify the fonts used in the design. This can be done in a message if you want. We typically use Zinthra Fonts and Velkor Fonts.

CONTENT:
We're always open to different content and ideas. We often submit designs with stock images so the client can see our vision. We typically take pictures after the website launch to use their images with our vision. Lorem Ipsum is fine for paragraphs, but we ask that you write the headers in correct English. We want to be able to show the vision and identify the sections of the website.

INSPIRATION:
We typically add a couple of links in the brief of websites we like to help you get started in your design.

REVISIONS:
We do not often ask for revisions of the designs unless we see something in the design that may not appeal to the client. If there are slight changes that we want to make, we do that in the development process.

FEEDBACK:
We rarely give feedback on designs during the design process. We are working on many website projects and do not have the time to provide feedback. We usually respond if your request is well thought out and asks specific questions, but a note asking “feedback, please” usually goes unanswered

```html
<!DOCTYPE html>
<html lang="en">
<head>
<meta charset="utf-8">
<title>Kestrel Meadow Guild of Realtors</title>
<link href="https://fonts.googleapis.com/css2?family=Poppins:wght@400;500;600;700&family=Lato:wght@400;700;900&display=swap" rel="stylesheet">
<style>
:root{
  --teal:#22b0cf;
  --navy:#0c2c54;
  --blue:#1767a8;
  --yellow:#fdd20a;
  --pale:#eef4fb;
  --ink:#222;
  --muted:#555;
  --black:#050505;
}
*{box-sizing:border-box;margin:0;padding:0}
html,body{width:1200px;height:4354px;overflow:hidden}
body{position:relative;font-family:"Poppins",sans-serif;color:var(--ink);background:#fff}
.abs{position:absolute}
.btn{position:absolute;background:var(--yellow);color:#111;font:700 13px "Lato",sans-serif;text-transform:uppercase;border-radius:4px;display:flex;align-items:center;justify-content:center;gap:5px;letter-spacing:.2px}
.btn i{width:11px;height:11px;border-radius:50%;background:#111;display:inline-block;position:relative}
.btn i:after{content:"";position:absolute;left:3px;top:3px;border-left:5px solid var(--yellow);border-top:2.5px solid transparent;border-bottom:2.5px solid transparent}
.topbar{left:0;top:0;width:1200px;height:45px;background:var(--teal);color:#fff;font-size:12px}
.nav{left:0;top:45px;width:1200px;height:42px;background:#fff;font-size:14px}
.nav a{position:absolute;top:12px;color:#222;text-decoration:none}
.brand{font:700 26px "Poppins",sans-serif;color:var(--blue);letter-spacing:-1px}
.tag{font-size:7px;color:var(--blue);white-space:nowrap}
.hero{left:0;top:87px;width:1200px;height:635px}
.hero h4{color:var(--teal);font:600 22px "Poppins",sans-serif}
.hero h1{color:#fff;font:600 33px/1.35 "Poppins",sans-serif}
.hero p{color:#fff;font-size:14px;line-height:29px}
.pill-title{position:absolute;width:280px;text-align:center;font:600 23px/1.4 "Poppins",sans-serif}
.about{left:0;top:1242px;width:1200px;height:550px;background:var(--pale)}
.h2{font:700 32px "Lato",sans-serif;color:var(--navy);text-transform:uppercase;line-height:1.3}
.h2 span{color:var(--blue)}
.h2 em{font-style:normal;color:var(--teal)}
.about p{font-size:14px;line-height:23px;color:var(--muted);text-align:justify}
.stats{left:0;top:1792px;width:1200px;height:338px;background:linear-gradient(90deg,#22b0d0,#1273b4)}
.stat{position:absolute;top:58px;width:230px;text-align:center;color:#fff}
.stat .ic{width:96px;height:96px;border-radius:50%;background:#fff;margin:0 auto 14px;display:flex;align-items:center;justify-content:center}
.stat b{display:block;font:700 30px "Lato",sans-serif;margin-bottom:6px}
.stat p{font-size:13px;line-height:22px}
.card{position:absolute;top:2308px;width:308px;height:396px}
.card .img{position:absolute;left:0;top:0;width:308px;height:227px}
.card .body{position:absolute;left:7px;top:195px;width:294px;height:200px;background:#fff;box-shadow:0 4px 14px rgba(0,0,0,.12);border-radius:4px;padding:18px 22px}
.card h3{font:700 20px "Lato",sans-serif;color:var(--navy);margin-bottom:6px}
.card p{font-size:14px;line-height:25px;color:var(--muted)}
.team{left:0;top:2765px;width:1200px;height:531px;background:linear-gradient(#f4f6f9,#fff)}
.member{position:absolute;font:500 20px "Lato",sans-serif;color:var(--navy);text-align:center;width:240px}
.member-role{position:absolute;font:400 19px "Poppins",sans-serif;color:var(--navy);text-align:center;width:240px}
.mapbg{left:0;top:3296px;width:1200px;height:700px;background:linear-gradient(160deg,#eef1f2,#dfe6e4 60%,#e7ece9)}
.form{left:242px;top:3642px;width:752px;height:350px;background:#fff;box-shadow:0 0 10px rgba(0,0,0,.08)}
.field{position:absolute;border:1.5px solid #bbb;height:44px;font-size:14px;color:#333;padding:12px 18px}
.footer{left:0;top:3960px;width:1200px;height:394px;background:var(--black);color:#fff}
.footer h5{font:500 24px "Lato",sans-serif;margin-bottom:12px}
.footer li{list-style:none;font-size:13px;line-height:28px}
.ficon{width:26px;height:26px;border-radius:50%;background:var(--yellow);display:inline-block;vertical-align:middle;margin-right:14px}
</style>
</head>
<body>

<div class="abs topbar">
  <svg class="abs" style="left:102px;top:15px" width="10" height="14" viewBox="0 0 10 14"><path d="M5 0a5 5 0 0 1 5 5c0 4-5 9-5 9S0 9 0 5a5 5 0 0 1 5-5z" fill="#fff"/><circle cx="5" cy="5" r="2" fill="#22b0cf"/></svg>
  <span class="abs" style="left:126px;top:14px">48 Larkspur Way, 3rd Floor Kestrel Meadow, CA 95201</span>
  <svg class="abs" style="left:848px;top:17px" width="14" height="10" viewBox="0 0 14 10"><rect width="14" height="10" rx="1" fill="#fff"/><path d="M0 0l7 6 7-6" stroke="#22b0cf" fill="none"/></svg>
  <span class="abs" style="left:872px;top:14px">info@kmguild.org</span>
  <span class="abs" style="left:1010px;top:17px;width:10px;height:10px;border-radius:50%;background:#fff"></span>
  <span class="abs" style="left:1035px;top:17px;width:10px;height:10px;border-radius:50%;background:#fff"></span>
  <span class="abs" style="left:1060px;top:17px;width:10px;height:10px;border-radius:50%;background:#fff"></span>
  <span class="abs" style="left:1085px;top:17px;width:10px;height:10px;border-radius:50%;background:#fff"></span>
</div>

<div class="abs nav">
  <a style="left:104px">About</a>
  <a style="left:177px">Education</a>
  <a style="left:276px">Advocacy</a>
  <a style="left:375px">Legal</a>
  <a style="left:701px">Industry News &amp; Information</a>
  <svg class="abs" style="left:924px;top:5px" width="32" height="32" viewBox="0 0 32 32"><circle cx="16" cy="16" r="16" fill="#1767a8"/><path d="M11 9l3 0 1 4-2 1a9 9 0 0 0 5 5l1-2 4 1 0 3c-7 1-13-5-12-12z" fill="#fff"/></svg>
  <span class="abs" style="left:974px;top:2px;font-size:12px;color:var(--teal);font-weight:500">How Can We Help:</span>
  <span class="abs" style="left:974px;top:20px;font-size:12px;font-weight:600">(555) 310-2274</span>
</div>
<svg class="abs" style="left:512px;top:30px" width="176" height="82" viewBox="0 0 176 82"><polygon points="0,0 176,0 176,54 88,82 0,54" fill="#fff"/></svg>
<div class="abs brand" style="left:0;width:1200px;text-align:center;top:40px;font-size:27px">KMGR</div>
<div class="abs tag" style="left:0;width:1200px;text-align:center;top:75px">WE EMPOWER • WE EDUCATE • WE CONNECT</div>

<div class="abs hero">
  <div role="img" aria-label="Photo of two smiling real estate agents reviewing a tablet in a bright office" class="abs" style="left:0;top:0;width:1200px;height:635px;background:linear-gradient(90deg,#1d1a17 0%,#3a3128 40%,#6b5a46 70%,#3e3a34 100%)"></div>
  <svg class="abs" style="left:0;top:490px" width="1200" height="145" viewBox="0 0 1200 145"><polygon points="0,85 600,145 1200,85 1200,145 0,145" fill="#fff"/><polygon points="0,85 600,145 1200,85 1200,105 600,135 0,105" fill="#1ba7c9"/><polygon points="0,67 0,85 600,145 596,122" fill="#1ba7c9"/><polygon points="1200,67 1200,85 600,145 604,122" fill="#1ba7c9"/></svg>
  <h4 class="abs" style="left:104px;top:122px">Welcome To</h4>
  <h1 class="abs" style="left:104px;top:154px;width:520px">Kestrel Meadow<br>Guild of Realtors</h1>
  <p class="abs" style="left:104px;top:253px;width:380px">Lorem ipsum dolor sit amet, consectetur adipiscing elit, sed do eiusmod tempor incididunt ut labore et dolore magna aliqua.</p>
  <div class="btn" style="left:104px;top:358px;width:143px;height:40px">Get Started <i></i></div>
</div>

<svg class="abs" style="left:0;top:800px" width="1200" height="340" viewBox="0 0 1200 340">
  <defs><filter id="sh" x="-20%" y="-20%" width="140%" height="140%"><feDropShadow dx="0" dy="3" stdDeviation="6" flood-color="#000" flood-opacity=".12"/></filter></defs>
  <g filter="url(#sh)">
    <polygon points="242,12 382,92 382,252 242,332 102,252 102,92" fill="#fff"/>
    <polygon points="600,12 740,92 740,252 600,332 460,252 460,92" fill="#0c2c54"/>
    <polygon points="957,12 1097,92 1097,252 957,332 817,252 817,92" fill="#fff"/>
  </g>
  <circle cx="243" cy="118" r="49" fill="#0c2c54"/>
  <circle cx="600" cy="118" r="49" fill="#fdd20a"/>
  <circle cx="966" cy="118" r="49" fill="#0c2c54"/>
  <path d="M222 140h42M230 140v-16h8v16M240 140v-26h8v26M250 140v-36h8v36" stroke="#fdd20a" stroke-width="3" fill="none"/>
  <path d="M578 100c8-4 16-4 22 2 6-6 14-6 22-2v38c-8-4-16-4-22 2-6-6-14-6-22-2z" fill="#0c2c54"/>
  <rect x="948" y="98" width="36" height="40" rx="3" fill="#fdd20a"/>
  <path d="M954 108h24M954 116h24M954 124h16" stroke="#0c2c54" stroke-width="3"/>
  <circle cx="240" cy="302" r="23" fill="#0c2c54"/>
  <circle cx="595" cy="302" r="23" fill="#fdd20a"/>
  <circle cx="953" cy="302" r="23" fill="#0c2c54"/>
  <path d="M232 302h14m-5-6 6 6-6 6" stroke="#fff" stroke-width="3" fill="none"/>
  <path d="M587 302h14m-5-6 6 6-6 6" stroke="#0c2c54" stroke-width="3" fill="none"/>
  <path d="M945 302h14m-5-6 6 6-6 6" stroke="#fff" stroke-width="3" fill="none"/>
</svg>
<div class="pill-title" style="left:102px;top:985px;color:var(--teal)">We<br>Empower</div>
<div class="pill-title" style="left:460px;top:985px;color:#fff">We<br>Educate</div>
<div class="pill-title" style="left:827px;top:985px;color:var(--teal)">We<br>Connect</div>

<div class="abs about">
  <svg class="abs" style="left:152px;top:57px" width="366" height="422" viewBox="0 0 366 422">
    <linearGradient id="ag" x1="0" y1="0" x2="1" y2="1"><stop offset="0" stop-color="#e9ebe6"/><stop offset=".5" stop-color="#c9c2b5"/><stop offset="1" stop-color="#8c8676"/></linearGradient>
    <clipPath id="hx"><polygon points="183,22 346,116 346,306 183,400 20,306 20,116"/></clipPath>
    <polygon points="183,4 362,107 362,315 183,418 4,315 4,107" fill="none" stroke="#1767a8" stroke-width="5"/>
    <rect role="img" aria-label="Photo of an agent shaking hands with senior clients at a table" x="0" y="0" width="366" height="422" fill="url(#ag)" clip-path="url(#hx)"/>
  </svg>
  <div class="abs h2" style="left:639px;top:116px;width:470px"><em>About</em> Kestrel Meadow Guild of Realtors</div>
  <p class="abs" style="left:639px;top:204px;width:456px">Lorem ipsum dolor sit amet, consectetur adipiscing elit, sed do eiusmod tempor incididunt ut labore et dolore magna aliqua. Ut enim ad minim veniam, quis nostrud exercitation ullamco laboris nisi ut aliquip ex ea commodo consequat. Duis aute irure dolor in reprehenderit in voluptate velit esse cillum dolore eu fugiat nulla pariatur. Excepteur sint occaecat cupidatat non proident, sunt in culpa qui officia deserunt mollit anim id est laborum.</p>
  <div class="btn" style="left:639px;top:414px;width:127px;height:40px">Read More <i></i></div>
</div>

<div class="abs stats">
  <div class="stat" style="left:100px"><div class="ic"><svg width="50" height="44" viewBox="0 0 50 44"><rect x="2" y="6" width="46" height="36" rx="4" fill="none" stroke="#0c2c54" stroke-width="3"/><text x="25" y="32" font-family="Lato" font-weight="900" font-size="15" fill="#0c2c54" text-anchor="middle">YEAR</text></svg></div><b>1.5 MILLION+</b><p>Lorem ipsum dolor sit amet, consectetur adipiscing elit, sed do eiusmod tempor incididunt</p></div>
  <div class="stat" style="left:362px"><div class="ic"><svg width="50" height="54" viewBox="0 0 50 54"><path d="M5 52V18h12V6h16v12h12v34z" fill="#0c2c54"/><path d="M11 26v6M11 38v6M22 14v6M28 14v6M22 26v6M28 26v6M22 38v6M28 38v6M39 26v6M39 38v6" stroke="#fff" stroke-width="3"/></svg></div><b>116 Years</b><p>Lorem ipsum dolor sit amet, consectetur adipiscing elit, sed do eiusmod tempor incididunt</p></div>
  <div class="stat" style="left:624px"><div class="ic"><svg width="50" height="50" viewBox="0 0 50 50"><path d="M6 20h16v-6a5 5 0 0 1 10 0v6h10v26H6z" fill="#0c2c54"/></svg></div><b>1,200</b><p>Lorem ipsum dolor sit amet, consectetur adipiscing elit, sed do eiusmod tempor incididunt</p></div>
  <div class="stat" style="left:886px"><div class="ic"><svg width="50" height="50" viewBox="0 0 50 50"><rect x="6" y="10" width="34" height="36" fill="none" stroke="#0c2c54" stroke-width="4"/><path d="M12 40h22M12 32h14" stroke="#0c2c54" stroke-width="3"/><path d="M30 26 46 8" stroke="#0c2c54" stroke-width="5"/></svg></div><b style="font-size:42px;margin-top:-8px;margin-bottom:0">200,000+</b><p>Lorem ipsum dolor sit amet, consectetur adipiscing elit, sed do eiusmod tempor incididunt</p></div>
</div>

<div class="abs h2" style="left:0;width:1200px;text-align:center;top:2222px"><em>Our</em> Projects</div>
<div class="card" style="left:104px">
  <div class="img" role="img" aria-label="Photo of a blue suburban family home under an evening sky" style="background:linear-gradient(#6c8ea3,#cfd8d9 55%,#3d5a3a)"></div>
  <div class="body"><h3>Advice For Buyers</h3><p>Lorem ipsum dolor sit amet, consectetur adipiscing elit, sed do eiusmod tempor incididunt ut</p><div class="btn" style="left:22px;top:132px;width:127px;height:40px">Read More <i></i></div></div>
</div>
<div class="card" style="left:446px">
  <div class="img" role="img" aria-label="Photo of professionals discussing plans in a meeting" style="background:linear-gradient(120deg,#3e4b55,#8a9aa3 50%,#2f3a42)"></div>
  <div class="body"><h3>Advice For Sellers</h3><p>Lorem ipsum dolor sit amet, consectetur adipiscing elit, sed do eiusmod tempor incididunt ut</p><div class="btn" style="left:22px;top:132px;width:127px;height:40px">Read More <i></i></div></div>
</div>
<div class="card" style="left:788px">
  <div class="img" role="img" aria-label="Photo of a family sitting on a sofa under a cardboard roof" style="background:linear-gradient(#ece6dc,#b89f83 60%,#6d5c4a)"></div>
  <div class="body"><h3>Renting Out Your Home</h3><p>Lorem ipsum dolor sit amet, consectetur adipiscing elit, sed do eiusmod tempor incididunt ut</p><div class="btn" style="left:22px;top:132px;width:127px;height:40px">Read More <i></i></div></div>
</div>

<div class="abs team">
  <div class="abs h2" style="left:0;width:1200px;text-align:center;top:90px"><span style="color:var(--navy)">Our</span> <span>Team</span></div>
  <svg class="abs" style="left:0;top:175px" width="1200" height="260" viewBox="0 0 1200 260">
    <polygon role="img" aria-label="Portrait photo of a team member in a dark suit" points="228,4 324,58 324,166 228,220 132,166 132,58" fill="#8f959b"/>
    <polygon role="img" aria-label="Portrait photo of a team member in a grey suit" points="477,4 573,58 573,166 477,220 381,166 381,58" fill="#a49a8e"/>
    <polygon points="725,4 823,60 823,172 725,228 627,172 627,60" fill="#fdd20a" stroke="#22b0cf" stroke-width="3"/>
    <polygon role="img" aria-label="Portrait photo of a team member in a white blouse" points="979,4 1075,58 1075,166 979,220 883,166 883,58" fill="#b7b3ad"/>
    <circle cx="684" cy="155" r="12" fill="#fff"/><circle cx="724" cy="155" r="12" fill="#fff"/><circle cx="766" cy="155" r="12" fill="#fff"/>
    <circle cx="684" cy="155" r="4" fill="#1767a8"/><circle cx="724" cy="155" r="4" fill="#1767a8"/><circle cx="766" cy="155" r="4" fill="#1767a8"/>
    <circle cx="725" cy="230" r="24" fill="#22b0cf"/>
    <path d="M721 220l9 10-9 10" stroke="#fff" stroke-width="2.5" fill="none"/>
  </svg>
  <div class="member" style="left:605px;top:262px;font-weight:700">Owen Prescott</div>
  <div class="member-role" style="left:605px;top:290px">Partner</div>
  <div class="member" style="left:88px;top:420px">Ellis Carrow</div>
  <div class="member" style="left:357px;top:420px">Dane Whitlock</div>
  <div class="member" style="left:859px;top:420px">Nora Vantell</div>
</div>

<div class="abs mapbg" role="img" aria-label="Street map of Kestrel Meadow and surrounding area"></div>
<div class="abs h2" style="left:0;width:1200px;text-align:center;top:3348px"><span>Contact</span> <em style="color:var(--blue)">Us</em></div>
<svg class="abs" style="left:0;top:3890px" width="1200" height="90" viewBox="0 0 1200 90"><polygon points="0,52 242,8 242,70 0,90" fill="#1ba7c9"/><polygon points="1200,52 994,8 994,70 1200,90" fill="#1ba7c9"/></svg>
<div class="abs footer">
  <svg class="abs" style="left:0;top:0" width="1200" height="40" viewBox="0 0 1200 40"><polygon points="0,0 0,16 242,0" fill="#e2e8e6"/><polygon points="1200,0 1200,16 994,0" fill="#e2e8e6"/></svg>
  <div class="abs brand" style="left:76px;top:173px;font-size:38px;width:250px;text-align:center">KMGR</div>
  <div class="abs tag" style="left:76px;top:222px;width:250px;text-align:center;font-size:11px">WE EMPOWER • WE EDUCATE • WE CONNECT</div>
  <div class="abs" style="left:365px;top:130px"><h5>Quick Links</h5><ul><li>About</li><li>Education</li><li>Advocacy</li><li>Legal</li><li>Industry News &amp;<br>Information</li></ul></div>
  <div class="abs" style="left:551px;top:130px;width:240px"><h5>Headquarters</h5>
    <div style="display:flex;font-size:13px;line-height:20px;margin-top:8px"><span class="ficon" style="flex:none"></span>48 Larkspur Way, 3rd Floor Kestrel Meadow, CA 95201</div>
    <div style="font-size:13px;margin-top:16px"><span class="ficon"></span>+1 555 555 0148</div>
    <div style="font-size:13px;margin-top:16px"><span class="ficon"></span>info@kmguild.org</div>
  </div>
  <div class="abs" style="left:821px;top:130px;width:300px"><h5>Inquiries</h5>
    <p style="font-size:11px;line-height:19px">For any inquiries, questions or commendations, please call: +1 555 555 0148 or fill out the following form</p>
    <div style="margin-top:12px;width:288px;height:40px;border:2px solid var(--yellow);border-radius:4px;font-size:11px;padding:11px 12px;position:relative">Enter Email
      <svg style="position:absolute;right:14px;top:12px" width="14" height="13" viewBox="0 0 14 13"><path d="M0 6 14 0 10 13 7 8z" fill="#fff"/></svg></div>
  </div>
  <div class="abs" style="left:0;width:1200px;text-align:center;top:350px;font-size:13px;font-weight:500">©2024. ALL RIGHTS RESERVED.</div>
</div>
<div class="abs form">
  <div class="field" style="left:29px;top:36px;width:340px">First Name</div>
  <div class="field" style="left:385px;top:36px;width:340px">Last Name</div>
  <div class="field" style="left:29px;top:96px;width:340px">Phone Number</div>
  <div class="field" style="left:385px;top:96px;width:340px">Email</div>
  <div class="field" style="left:29px;top:157px;width:696px;height:112px">Message</div>
  <div class="btn" style="left:294px;top:295px;width:126px;height:40px">Submit <i></i></div>
</div>

</body>
</html>
```